Wordpress Website for Trauma Ward Harm Recovery Outreach Scheme

We are looking for a wordpress website that is clean, crisp and bold for our Trauma Ward Harm Recovery Outreach Scheme.

We are a Canadian hospital in Winnipeg, MB which sees many youth injured by violence. We are starting up an Trauma Ward Harm Recovery Outreach Scheme for youth injured by violence. The youth who we will serve will be between the age of 14 - 24 and many will be gang-involved.

However, it is important to note that this website isn't for the youth themselves as much as it is for professionals and community interested in learning about our program. As such, it is should be friendly but professional. I am interested in a bold, crisp look.

I have attached our logo file for your use.
Updates

I forgot to mention that there should be a section along the bottom to include logos of funders and partners.

Also would be nice to include a spot for viewers to automatically subscribe to our newsletter by putting their email in.

I have added in a file of text that I will use - but want to easily be able to change and update (and post links etc). 

Target Market(s)

This will target a professional and community audience. We would like a crisp, bold, professional presence

Industry/Entity Type

Hospital

Requirements
Must have
• I would like a navigation bar that includes the following:

About TW-ROS (Background and Research sections)
People
Latest News
Job Opportunities
Research Opportunities
Publications & Reports
Contact TW-ROS ( a form)

I would also like a search form and a link to twitter.

While I am comfortable with Wordpress - I am not an expert. I want this to be as simple as possible for me to update.
Nice to have
• We have a great logo and only a few photos which I will upload in the next day.

We could also use stock photos for now but overtime switch these with photos of our own hospital emergency department and team. Additionally, we would like some stock photos of youth - a diverse mix but to include Aboriginal/First Nations, immigrant and caucasian youth
Should not have
• This design should not have guns, knifes, alcohol or blood/gore in there (I've learned to state this after using pixel throng for the logo! )

```html
<!DOCTYPE html>
<html lang="en">
<head>
<meta charset="utf-8">
<title>TW-ROS — Trauma Ward Harm Recovery Outreach Scheme</title>
<link rel="stylesheet" href="https://fonts.googleapis.com/css2?family=PT+Sans:ital,wght@0,400;0,700;1,400&display=swap">
<style>
:root{
  --red:#c9473a;
  --red-dark:#8b1f24;
  --ink:#222;
  --text:#444;
  --muted:#777;
  --rule:#d6d6d6;
  --footer:#ebebeb;
  --white:#fff;
}
*{box-sizing:border-box;margin:0;padding:0}
html,body{width:1200px;height:1148px;overflow:hidden;background:var(--white)}
body{font-family:"PT Sans",Arial,sans-serif;color:var(--text);position:relative}
.abs{position:absolute}
a{color:inherit;text-decoration:none}

.brand{left:180px;top:18px;display:flex;align-items:center;gap:10px}
.brand-mark{width:14px;height:14px;background:var(--red-dark)}
.brand-name{font-size:30px;font-weight:700;color:var(--red-dark);letter-spacing:.5px;line-height:1}
.brand-full{position:absolute;left:180px;top:54px;width:230px;font-size:11.5px;color:var(--muted);line-height:1.3}

.util-nav{right:182px;top:30px;font-size:10px;color:var(--ink);display:flex;gap:0}
.util-nav span.sep{margin:0 16px;color:var(--ink)}
.call{right:182px;top:56px;display:flex;align-items:center;gap:7px;color:var(--red);font-size:15.5px;font-weight:700}
.call svg{display:block}

.main-nav{left:180px;top:106px;width:840px;height:38px;background:var(--red);border-radius:3px;display:flex;justify-content:space-around;align-items:center;color:var(--white);font-size:12.5px;text-transform:uppercase;padding:0 20px}

.hero{left:180px;top:149px;width:840px;height:338px;border-radius:3px;
  background:linear-gradient(180deg,#5f6f80 0%,#8b8f96 35%,#b79a82 55%,#7a7068 62%,#5a6470 100%)}
.hero-copy{left:737px;top:272px;color:var(--white);text-transform:uppercase}
.hero-copy .big{font-size:33px;font-weight:700;line-height:1}
.hero-copy .small{font-size:16.5px;font-weight:700;line-height:24px;margin-top:6px}
.dots{left:954px;top:465px;display:flex;gap:4px}
.dots i{width:9px;height:9px;background:#8a8f95;display:block}
.dots i.on{background:var(--red)}

.welcome{left:180px;top:504px;width:840px;text-align:center}
.welcome h1{font-size:20px;color:var(--red);font-weight:700;text-transform:uppercase}
.welcome h2{font-size:19px;color:var(--ink);font-weight:400;text-transform:uppercase;margin-top:8px}
.welcome p{font-size:9.2px;line-height:15.5px;margin:9px 12px 0}

.col{top:647px;width:222px}
.col h3{font-size:13.5px;color:var(--red);text-transform:uppercase;font-weight:700}
.col .ph{width:222px;height:94px;margin-top:14px}
.col p{font-size:9px;line-height:15.5px;margin-top:15px}
.btn{display:inline-block;background:var(--red);color:var(--white);font-size:9px;font-weight:700;width:71px;height:21px;line-height:21px;text-align:center;border-radius:2px}
.col .btn{position:absolute;top:210px;left:0}

.news{left:694px;top:647px;width:326px}
.news h3{font-size:13.5px;color:var(--red);text-transform:uppercase;font-weight:700}
.item{position:absolute;left:0;width:326px}
.item .thumb{position:absolute;left:0;top:0;width:85px;height:69px}
.item .body{position:absolute;left:103px;top:0;width:220px}
.item h4{font-size:10px;color:var(--red);font-weight:400;text-transform:uppercase}
.item p{font-size:9px;line-height:15.5px;margin-top:5px}
.item em{display:block;font-size:9px;color:var(--red);margin-top:5px}
.news .btn{position:absolute;left:0;top:210px}

.divider{left:180px;top:905px;width:840px;height:1px;background:var(--rule)}
.partners-h{left:180px;top:919px;font-size:13.5px;color:var(--red);font-weight:700;text-transform:uppercase}
.badge{top:949px;width:129px;height:60px;border:1px solid #cfcfcf;display:flex;align-items:center;justify-content:center}
.badge span{display:block;width:84px;height:20px;background:#d8dde3;border-radius:3px}

.footer{left:180px;top:1031px;width:840px;height:73px;background:var(--footer);border-radius:3px}
.f-nav{left:27px;top:23px;font-size:8px;color:#555;text-transform:uppercase;white-space:nowrap}
.f-nav .sep{margin:0 9px}
.f-copy{left:27px;top:44px;font-size:8px;color:#555}
.f-news{left:484px;top:16px;font-size:12px;color:var(--red);font-weight:700;text-transform:uppercase}
.f-form{left:482px;top:37px;width:199px;height:21px;background:var(--white);border:1px solid #d8d8d8;border-radius:3px}
.f-form .ph-txt{position:absolute;left:10px;top:5px;font-size:7.5px;color:#666}
.f-form .btn{position:absolute;right:0;top:-1px;width:52px;height:21px;line-height:21px;font-size:7.5px}
.social{left:715px;top:26px;display:flex;gap:4px}
.social i{display:block;width:24px;height:24px;border-radius:50%}
</style>
</head>
<body>

<header>
  <div class="brand abs"><span class="brand-mark"></span><span class="brand-name">TW-ROS</span></div>
  <div class="brand-full">Trauma Ward Harm Recovery Outreach Scheme</div>

  <nav class="util-nav abs"><a href="#">HOME</a><span class="sep">|</span><a href="#">ABOUT</a><span class="sep">|</span><a href="#">CONTACT US</a></nav>
  <div class="call abs">
    <svg width="30" height="30" viewBox="0 0 30 30" aria-hidden="true"><circle cx="15" cy="15" r="13.5" fill="none" stroke="#bbb" stroke-width="1.5"/><path d="M11 9.5c-1 1-1.2 3 .6 5.6s4 4.4 6 5.1c1.3.4 2.4 0 3-.7l-2-2.1c-.4.4-1 .5-1.6.1-1.2-.8-2.4-2-3.3-3.3-.4-.6-.3-1.2.1-1.6z" fill="#aaa"/></svg>
    <span>CALL US : ( 204 ) 555 0142</span>
  </div>

  <nav class="main-nav abs"><a href="#">People</a><a href="#">Latest News</a><a href="#">Job Opportunities</a><a href="#">Research Opportunities</a><a href="#">Publications &amp; Reports</a></nav>
</header>

<section>
  <div class="hero abs" role="img" aria-label="Silhouettes of youth cartwheeling on a beach at sunset, reflected on wet sand"></div>
  <div class="hero-copy abs"><div class="big">We are a</div><div class="small">Hospital take care of people<br>injured in violence</div></div>
  <div class="dots abs"><i class="on"></i><i></i><i></i><i></i></div>
</section>

<section class="welcome abs">
  <h1>Welcome to TW-ROS</h1>
  <h2>Trauma Ward Harm Recovery Outreach Scheme</h2>
  <p>Youth injured by violence is a concerning issue in Canada. Youth homicide is the fourth most common reason of death among youth in Canada and in some provinces, the most common reason for visiting an emergency department. Even more concerning is that there is a high repeat rate of visits to emergency departments for subsequent injuries caused by violence. At the Riverside Health Centre, 20% of youth injured by violence return for a subsequent injury within the next year.</p>
</section>

<section class="col abs" style="left:180px">
  <h3>TW-ROS Research</h3>
  <div class="ph" role="img" aria-label="Photo of a consultant in discussion with a colleague" style="background:linear-gradient(135deg,#9fb6cc,#d6c9bf 60%,#e9e2da)"></div>
  <p>The “BridgeWay Care for Youth Harmed by Violence” Study is a pilot randomized control trial designed to examining recruitment, feasibility and program safety prior to launching a larger effectiveness trial...</p>
  <a class="btn" href="#">Read more</a>
</section>

<section class="col abs" style="left:437px">
  <h3>Publications &amp; Reports</h3>
  <div class="ph" role="img" aria-label="Photo of a stack of folded newspapers" style="background:linear-gradient(180deg,#8d8d8d,#d9d9d9 45%,#9a9a9a 80%,#eeeeee)"></div>
  <p>The “BridgeWay Care for Youth Harmed by Violence” Study is a pilot randomized control trial designed to examining recruitment, feasibility and program safety prior to launching a larger effectiveness trial...</p>
  <a class="btn" href="#">Read more</a>
</section>

<section class="news abs">
  <h3>Latest News</h3>
  <div class="item" style="top:33px">
    <div class="thumb" role="img" aria-label="Silhouettes of young people against an orange sky" style="background:linear-gradient(180deg,#6d7888,#c88a4e 70%,#3a2c24)"></div>
    <div class="body"><h4>The Youth Violence Research Program</h4><p>The “BridgeWay Care for Youth Harmed by Violence” Study is a pilot randomized control...</p><em>Posted on 24 June 2013,</em></div>
  </div>
  <div class="item" style="top:123px">
    <div class="thumb" role="img" aria-label="Photo of medical staff caring for a patient" style="background:linear-gradient(135deg,#7fb6c8,#e5edf1 55%,#b9d3de)"></div>
    <div class="body"><h4>The Youth Violence Research Program</h4><p>The “BridgeWay Care for Youth Harmed by Violence” Study is a pilot randomized control...</p><em>Posted on 24 June 2013,</em></div>
  </div>
  <a class="btn" href="#">View more</a>
</section>

<div class="divider abs"></div>
<h3 class="partners-h abs">Funders &amp; Partners</h3>
<div class="badge abs" style="left:180px"><span></span></div>
<div class="badge abs" style="left:322px"><span></span></div>
<div class="badge abs" style="left:464px"><span></span></div>
<div class="badge abs" style="left:607px"><span></span></div>
<div class="badge abs" style="left:749px"><span></span></div>
<div class="badge abs" style="left:892px"><span></span></div>

<footer class="footer abs">
  <nav class="f-nav abs">People<span class="sep">|</span>Latest News<span class="sep">|</span>Job Opportunities<span class="sep">|</span>Research Opportunities<span class="sep">|</span>Publications &amp; Reports</nav>
  <div class="f-copy abs">COPYRIGHTS © 2013. TWROS. ALL RIGHTS RESERVED.</div>
  <div class="f-news abs">Newsletter Signup</div>
  <div class="f-form abs"><span class="ph-txt">ENTER YOUR EMAIL ID :</span><a class="btn" href="#">SUBMIT</a></div>
  <div class="social abs"><i style="background:#3b5d9c"></i><i style="background:#4aa3df"></i><i style="background:#2c7fa8"></i><i style="background:#f0a020"></i></div>
</footer>

</body>
</html>
```